Brell Stone Company Business Cards

Front and Back Business Card - logo and text setup - cool design. I need workable photoshop or illustrator files so I can setup each employee card with design that is created
Updates

Hi everyone, thank you for the great entries. Please no more white and blue cards - there are so many already - black and silver only now please. thanks!

Target Market(s)

Construction Industry - Facility Managers

Industry/Entity Type

Construction

Contact Information for Business Card

I really like contemporary simplistic looks - clean neat....not opposed to seeing some black backrounds

Requirements
Must have
• Logo/website address with design on front only - www.brellstone-example.com (logo attached)
• Back:
• Name/Title/Company Address/Phone/email address
Nice to have
• Cool design
Should not have
• Nothing gimmicky like Fire or Water - since we are a Fire Protection company - it has all been done

```html
<!DOCTYPE html>
<html lang="en">
<head>
<meta charset="utf-8">
<title>Brell Stone Company – Business Cards</title>
<link rel="stylesheet" href="https://fonts.googleapis.com/css2?family=Arimo:wght@400;700&display=swap">
<style>
  :root {
    --stage: #2b2c31;
    --card: #111214;
    --silver: #c9ccd1;
    --silver-light: #eef0f2;
    --silver-dim: #8a8e95;
    --shadow: rgba(0, 0, 0, 0.45);
  }
  * { box-sizing: border-box; margin: 0; padding: 0; }
  html, body {
    width: 1200px; height: 800px; overflow: hidden;
    background: var(--stage);
    font-family: "Arimo", Arial, sans-serif;
  }
  .stage {
    width: 1200px; height: 800px;
    display: flex; align-items: center; justify-content: center; gap: 40px;
  }
  .card {
    position: relative;
    width: 520px; height: 300px;
    background: var(--card);
    border-radius: 22px;
    box-shadow: 0 14px 30px var(--shadow);
    overflow: hidden;
  }
  .card-art { position: absolute; inset: 0; width: 520px; height: 300px; }

  /* Front */
  .brand-name {
    position: absolute; left: 0; right: 0; top: 112px;
    text-align: center;
    font-weight: 700; font-size: 56px; letter-spacing: -1px;
    color: var(--silver-light); line-height: 1;
  }
  .brand-url {
    position: absolute; left: 0; right: 0; top: 200px;
    text-align: center;
    font-weight: 700; font-size: 11px; letter-spacing: 4px;
    color: var(--silver);
  }

  /* Back */
  .person {
    position: absolute; right: 245px; top: 128px;
    text-align: right;
  }
  .person-name { font-weight: 700; font-size: 24px; color: var(--silver-light); line-height: 1.05; }
  .person-title { font-size: 14px; color: var(--silver-dim); margin-top: 2px; }
  .contacts {
    position: absolute; left: 300px; top: 118px;
    list-style: none;
    font-size: 13px; color: var(--silver);
  }
  .contacts li { display: flex; align-items: center; gap: 8px; height: 22px; white-space: nowrap; }
  .contacts svg { width: 12px; height: 12px; flex: none; }
</style>
</head>
<body>
<main class="stage">

  <section class="card card-front" aria-label="Card front">
    <div class="brand-name">Brell Stone</div>
    <div class="brand-url">www.brellstone-example.com</div>
  </section>

  <section class="card card-back" aria-label="Card back">
    <svg class="card-art" viewBox="0 0 520 300" aria-hidden="true">
      <line class="rule rule-top" x1="40" y1="84" x2="480" y2="84" stroke="var(--silver-dim)" stroke-width="1"/>
      <line class="rule rule-divider" x1="285" y1="100" x2="285" y2="200" stroke="var(--silver)" stroke-width="1.5"/>
      <line class="rule rule-bottom" x1="40" y1="216" x2="480" y2="216" stroke="var(--silver-dim)" stroke-width="1"/>
    </svg>

    <div class="person">
      <div class="person-name">Dana Reyes</div>
      <div class="person-title">Director</div>
    </div>

    <ul class="contacts">
      <li>
        <svg viewBox="0 0 12 12" aria-label="Phone"><rect x="3" y="1" width="6" height="10" rx="1" fill="none" stroke="var(--silver)" stroke-width="1.3"/></svg>
        (555) 014 2280
      </li>
      <li>
        <svg viewBox="0 0 12 12" aria-label="Email"><rect x="1" y="2.5" width="10" height="7" fill="var(--silver)"/><path d="M1 2.5 L6 6.5 L11 2.5" fill="none" stroke="var(--card)" stroke-width="1"/></svg>
        hello@brellstone-example.com
      </li>
      <li>
        <svg viewBox="0 0 12 12" aria-label="Website"><circle cx="6" cy="6" r="5" fill="var(--silver)"/><path d="M1 6 H11 M6 1 V11 M6 1 C3 4 3 8 6 11 M6 1 C9 4 9 8 6 11" fill="none" stroke="var(--card)" stroke-width="0.7"/></svg>
        www.brellstone-example.com
      </li>
    </ul>
  </section>

</main>
</body>
</html>
```